Profesional personal website needs design and business card

I need a business card with my professional name as a logo "Dorian Vitality" for my business. I am a Wellness Coach, consultant and trainer. So it should be professional, wellness oriented and modern.

Target Market(s)

Private clients, governments, corporations. Luxury and high market.

Industry/Entity Type

Health And Wellness

Contact Information for Business Card

Dorian Vitality should be the logo

Colors

Designer to choose colors to be used in the design.

Requirements
Must have
• Dorian Vitality
• Name: Tomás Lirandel
• Wellness Coach, Consultant & Trainer.
• Website: www.dorianvitality-example.com
• Phone:
• Spain (+34) 612 480 317
• (USA) +1 (555) 610 4829
Nice to have
• The most important is the design of "Dorian Vitality", as this is going to be my personal brand logo. It should be professional, wellness, high end and actual.
Should not have
• no golds, no baroque style..

```html
<!DOCTYPE html>
<html lang="en">
<head>
<meta charset="utf-8">
<title>Dorian Vitality – Business Card</title>
<link href="https://fonts.googleapis.com/css2?family=Arimo:wght@400;700&display=swap" rel="stylesheet">
<style>
  :root {
    --backdrop: #3b3b3d;
    --brand-purple: #6f3a8d;
    --accent-green: #6db33f;
    --card-white: #f4f4f4;
    --ink: #1e1e1e;
    --rule: #555555;
  }
  * { margin: 0; padding: 0; box-sizing: border-box; }
  html, body {
    width: 1200px;
    height: 1021px;
    overflow: hidden;
    background: var(--backdrop);
    font-family: "Arimo", Arial, sans-serif;
  }
  .card {
    position: absolute;
    left: 220px;
    width: 760px;
    height: 434px;
    border-radius: 2px;
  }
  .card-back {
    top: 44px;
    background: var(--brand-purple);
    display: flex;
    align-items: center;
    justify-content: center;
  }
  .card-front {
    top: 534px;
    background: linear-gradient(100deg, #e8e8e8 0%, var(--card-white) 45%, #fafafa 100%);
  }
  .wordmark {
    display: flex;
    align-items: center;
    gap: 14px;
    font-weight: 700;
    letter-spacing: 0.5px;
    white-space: nowrap;
  }
  .wordmark-dot {
    border-radius: 50%;
    flex: none;
  }
  .card-back .wordmark { color: #ffffff; font-size: 52px; }
  .card-back .wordmark-dot { width: 26px; height: 26px; background: #ffffff; }
  .card-front .wordmark {
    position: absolute;
    left: 36px;
    top: 190px;
    color: var(--brand-purple);
    font-size: 34px;
    gap: 10px;
  }
  .card-front .wordmark-dot { width: 18px; height: 18px; background: var(--brand-purple); }
  .divider {
    position: absolute;
    left: 372px;
    top: 96px;
    width: 1px;
    height: 240px;
    background: var(--rule);
  }
  .contact {
    position: absolute;
    left: 400px;
    top: 108px;
    color: var(--ink);
  }
  .contact-name {
    color: var(--brand-purple);
    font-weight: 700;
    font-size: 29px;
    margin-bottom: 6px;
  }
  .contact-role {
    font-size: 21px;
    line-height: 26px;
  }
  .contact-lines {
    margin-top: 18px;
    list-style: none;
  }
  .contact-lines li {
    display: flex;
    align-items: center;
    gap: 8px;
    font-size: 20px;
    line-height: 28px;
    white-space: nowrap;
  }
  .contact-lines .website { font-size: 18px; }
  .contact-lines svg { width: 18px; height: 18px; flex: none; }
  .country { color: var(--brand-purple); margin-left: 4px; }
</style>
</head>
<body>

<section class="card card-back" aria-label="Business card back">
  <div class="wordmark"><span class="wordmark-dot"></span>Dorian Vitality</div>
</section>

<section class="card card-front" aria-label="Business card front">
  <div class="wordmark"><span class="wordmark-dot"></span>Dorian Vitality</div>
  <div class="divider"></div>
  <div class="contact">
    <h1 class="contact-name">Tomás Lirandel</h1>
    <p class="contact-role">Wellness Coach</p>
    <p class="contact-role">Consultant &amp; Trainer</p>
    <ul class="contact-lines">
      <li>
        <svg viewBox="0 0 24 24" aria-hidden="true"><path fill="#6db33f" d="M6.6 10.8a15.1 15.1 0 0 0 6.6 6.6l2.2-2.2c.3-.3.7-.4 1-.2 1.1.4 2.3.6 3.6.6.6 0 1 .4 1 1V20c0 .6-.4 1-1 1A17 17 0 0 1 3 4c0-.6.4-1 1-1h3.5c.6 0 1 .4 1 1 0 1.3.2 2.5.6 3.6.1.3 0 .7-.2 1z"/></svg>
        (+34) 612 480 317 <span class="country">Spain</span>
      </li>
      <li>
        <svg viewBox="0 0 24 24" aria-hidden="true"><path fill="#6db33f" d="M6.6 10.8a15.1 15.1 0 0 0 6.6 6.6l2.2-2.2c.3-.3.7-.4 1-.2 1.1.4 2.3.6 3.6.6.6 0 1 .4 1 1V20c0 .6-.4 1-1 1A17 17 0 0 1 3 4c0-.6.4-1 1-1h3.5c.6 0 1 .4 1 1 0 1.3.2 2.5.6 3.6.1.3 0 .7-.2 1z"/></svg>
        +1 (555) 610 4829 <span class="country">USA</span>
      </li>
      <li class="website">
        <svg viewBox="0 0 24 24" aria-hidden="true" fill="none" stroke="#6db33f" stroke-width="2"><circle cx="12" cy="12" r="9"/><ellipse cx="12" cy="12" rx="4" ry="9"/><line x1="3" y1="12" x2="21" y2="12"/></svg>
        www.dorianvitality-example.com
      </li>
    </ul>
  </div>
</section>

</body>
</html>
```